Im open to ideas.. I was thinking on my business cards aswell as my logo. a place for my name. email. phone number and abn..

ive attched a file with my business logo. which i dont love the colours.. i was think a dark background with charcoal letters so something along those colour schumes but im open to ideas..

BRM Constructions

```html
<!DOCTYPE html>
<html lang="en">
<head>
<meta charset="utf-8">
<title>BRM Constructions – Business Card</title>
<link rel="stylesheet" href="https://fonts.googleapis.com/css2?family=Montserrat:wght@400;500;600&display=swap">
<style>
  :root {
    --page-bg: #e6e4e0;
    --card-bg: #ffffff;
    --brand-red: #e2202e;
    --charcoal: #1c1c1c;
    --text-dark: #262626;
  }
  * { margin: 0; padding: 0; box-sizing: border-box; }
  html, body {
    width: 1200px;
    height: 1022px;
    overflow: hidden;
    background: var(--page-bg);
    font-family: "Montserrat", Arial, sans-serif;
  }
  .business-card {
    position: absolute;
    left: 75px;
    top: 211px;
    width: 1050px;
    height: 600px;
    background: var(--card-bg);
    border-radius: 26px;
    box-shadow: 0 10px 30px rgba(0, 0, 0, 0.12);
    display: flex;
    align-items: center;
  }
  .brand {
    width: 520px;
    padding-left: 80px;
    display: flex;
    align-items: center;
    gap: 18px;
  }
  .brand-square {
    width: 26px;
    height: 26px;
    background: var(--brand-red);
    flex: none;
  }
  .brand-name {
    font-weight: 600;
    font-size: 36px;
    letter-spacing: 1px;
    color: var(--charcoal);
    text-transform: uppercase;
    line-height: 1.1;
  }
  .contact {
    padding-left: 40px;
    color: var(--text-dark);
  }
  .person-name {
    font-weight: 500;
    font-size: 42px;
    letter-spacing: 2px;
    color: var(--brand-red);
    text-transform: uppercase;
    line-height: 1;
  }
  .person-role {
    font-size: 24px;
    margin-top: 8px;
  }
  .abn {
    font-size: 24px;
    margin-top: 10px;
  }
  .abn-label { color: var(--brand-red); font-weight: 500; }
  .contact-list {
    list-style: none;
    margin-top: 8px;
  }
  .contact-item {
    display: flex;
    align-items: center;
    gap: 14px;
    font-size: 24px;
    line-height: 1.45;
  }
  .contact-icon {
    width: 20px;
    height: 20px;
    flex: none;
    fill: var(--brand-red);
  }
  .web-domain { color: var(--brand-red); }
</style>
</head>
<body>
  <section class="business-card">
    <div class="brand">
      <span class="brand-square"></span>
      <span class="brand-name">BRM Constructions</span>
    </div>
    <div class="contact">
      <h1 class="person-name">Marcus Hale</h1>
      <p class="person-role">Director</p>
      <p class="abn"><span class="abn-label">ABN</span>: 61 208 453 719</p>
      <ul class="contact-list">
        <li class="contact-item">
          <svg class="contact-icon" viewBox="0 0 24 24" aria-hidden="true"><path d="M6.6 10.8a15.1 15.1 0 0 0 6.6 6.6l2.2-2.2a1 1 0 0 1 1-.25 11.4 11.4 0 0 0 3.6.57 1 1 0 0 1 1 1V20a1 1 0 0 1-1 1A17 17 0 0 1 3 4a1 1 0 0 1 1-1h3.5a1 1 0 0 1 1 1c0 1.25.2 2.45.57 3.6a1 1 0 0 1-.25 1z"/></svg>
          <span>+330 2791-4408</span>
        </li>
        <li class="contact-item">
          <svg class="contact-icon" viewBox="0 0 24 24" aria-hidden="true"><path d="M3 5h18v14H3zm2 2v.5l7 4.5 7-4.5V7zm0 2.9V17h14V9.9l-7 4.5z"/></svg>
          <span>info@brmconstructions.com</span>
        </li>
        <li class="contact-item">
          <svg class="contact-icon" viewBox="0 0 24 24" aria-hidden="true"><path d="M12 2a10 10 0 1 0 0 20 10 10 0 0 0 0-20zm6.9 6h-2.9a15.6 15.6 0 0 0-1.4-3.6A8 8 0 0 1 18.9 8zM12 4c.8 1.2 1.5 2.5 1.9 4h-3.8c.4-1.5 1.1-2.8 1.9-4zM4.3 14a8.2 8.2 0 0 1 0-4h3.4a16 16 0 0 0 0 4zm.8 2h2.9c.3 1.3.8 2.5 1.4 3.6A8 8 0 0 1 5.1 16zM8 8H5.1a8 8 0 0 1 4.3-3.6C8.8 5.5 8.3 6.7 8 8zm4 12c-.8-1.2-1.5-2.5-1.9-4h3.8c-.4 1.5-1.1 2.8-1.9 4zm2.3-6H9.7a14.6 14.6 0 0 1 0-4h4.6a14.6 14.6 0 0 1 0 4zm.3 5.6c.6-1.1 1.1-2.3 1.4-3.6h2.9a8 8 0 0 1-4.3 3.6zm1.7-5.6a16 16 0 0 0 0-4h3.4a8.2 8.2 0 0 1 0 4z"/></svg>
          <span>www.<span class="web-domain">brmconstructions</span>.com</span>
        </li>
      </ul>
    </div>
  </section>
</body>
</html>
```